Torvane Halbridge

Looking for modern business cards.
Clean contemporary design.
Similar to this.
https://www.plumvexa-search.example/imgres?imgurl=https%3A%2F%2Fimg.quorlint-cdn.example%2Fsleek_dark_metal_card_design_540.jpg&imgrefurl=https%3A%2F%2Fwww.quorlint-prints.example%2Fsleek_dark_metal_card_design-918273645501928374&q=modern%20business%20cards

But I'd like the blue to look metallic.

Business

```html
<!DOCTYPE html>
<html lang="en">
<head>
<meta charset="utf-8">
<title>Torvane Halbridge – Business Cards</title>
<link rel="stylesheet" href="https://fonts.googleapis.com/css2?family=Open+Sans:wght@300;400;600&family=Roboto+Condensed:wght@700&family=Roboto:wght@400;500&display=swap">
<style>
  :root {
    --stage: #e9e4dc;
    --paper: #f7f7f5;
    --navy: #1e4a6b;
    --teal: #27a3bf;
    --ink: #4a4f55;
    --rule: #27a3bf;
    --steel-dark: #2f86a6;
    --steel-mid: #4ea2c2;
    --steel-light: #7cc0d8;
    --white: #ffffff;
  }
  * { box-sizing: border-box; margin: 0; padding: 0; }
  html, body { width: 1200px; height: 886px; overflow: hidden; }
  body {
    background: var(--stage);
    display: flex;
    align-items: center;
    justify-content: center;
    gap: 64px;
  }
  .card {
    border-radius: 4px;
    box-shadow: 0 10px 30px rgba(60, 45, 30, 0.22);
  }
  .card-front {
    width: 360px;
    height: 630px;
    background: var(--paper);
    padding: 96px 30px 0;
    text-align: center;
  }
  .person-name {
    font-family: "Roboto Condensed", sans-serif;
    font-weight: 700;
    font-size: 34px;
    letter-spacing: 0.5px;
    color: var(--navy);
    line-height: 1;
  }
  .person-role {
    font-family: "Roboto", sans-serif;
    font-size: 17px;
    letter-spacing: 1px;
    color: var(--teal);
    margin-top: 6px;
  }
  .divider {
    width: 46px;
    height: 1px;
    background: var(--rule);
    margin: 22px auto;
  }
  .address, .contact {
    font-family: "Roboto", sans-serif;
    font-size: 15px;
    line-height: 1.5;
    color: var(--ink);
  }
  .contact dt {
    display: inline;
    font-weight: 500;
    color: var(--navy);
  }
  .contact dd { display: inline; margin-left: 4px; }
  .contact div { white-space: nowrap; }
  .card-back {
    width: 630px;
    height: 360px;
    background:
      repeating-linear-gradient(90deg, rgba(255,255,255,0.05) 0 1px, rgba(0,0,0,0.04) 1px 3px, rgba(255,255,255,0) 3px 5px),
      linear-gradient(115deg, var(--steel-light) 0%, var(--steel-mid) 30%, var(--steel-dark) 55%, var(--steel-mid) 78%, var(--steel-light) 100%);
    display: flex;
    flex-direction: column;
    align-items: center;
    justify-content: center;
    gap: 14px;
  }
  .brand {
    display: flex;
    align-items: center;
    gap: 18px;
  }
  .brand-name {
    font-family: "Open Sans", sans-serif;
    font-weight: 300;
    font-size: 44px;
    color: var(--white);
    letter-spacing: 0.5px;
  }
  .brand-dot {
    width: 30px;
    height: 30px;
    border-radius: 50%;
    background: var(--white);
  }
  .tagline {
    font-family: "Open Sans", sans-serif;
    font-size: 12px;
    letter-spacing: 3px;
    color: var(--white);
    opacity: 0.9;
  }
</style>
</head>
<body>
  <section class="card card-front">
    <h1 class="person-name">ILSA MARROW</h1>
    <p class="person-role">CEO/FOUNDER</p>
    <div class="divider"></div>
    <p class="address">4120 Quillfern Court<br>Dunmere, Oregon 97318</p>
    <div class="divider"></div>
    <dl class="contact">
      <div><dt>P:</dt><dd>555 214 0937</dd></div>
      <div><dt>E:</dt><dd>ilsa@torvanehalbridge.example</dd></div>
      <div><dt>W:</dt><dd>www.torvanehalbridge.example</dd></div>
    </dl>
  </section>

  <section class="card card-back">
    <div class="brand">
      <span class="brand-name">Torvane Halbridge</span>
      <span class="brand-dot"></span>
    </div>
    <p class="tagline">“Helping Good Ideas Grow Into Firm Ventures”</p>
  </section>
</body>
</html>
```